Banner dimension 1767 X 887 for Tovrelli website

Need one banner for our website www.tovrelli.com.au, The dimension of the banner should be 1767 x 887. Attached to this brief are two images that needs to be on that one banner, PLEASE DO NOT SEND SEPARATE BANNERS, both images on the same banner. Thanks

The banner should have the following message on it:

1.) " Take a further 40% off all stock" ( use code: TOVRELLI. Ends 31/12/2015)
2.) " Kick back or kick it up a notch this Autumn in the most versatile pique striped polo shirts and Pinafore belt strap denim dress"

Target Market(s)

kids aged 5-12yrs

Requirements
Must have
• very playful

```html
<!DOCTYPE html>
<html lang="en">
<head>
<meta charset="utf-8">
<title>Tovrelli Autumn Banner</title>
<link rel="stylesheet" href="https://fonts.googleapis.com/css2?family=Caveat+Brush&family=Gochi+Hand&family=Arimo:wght@400;700&display=swap">
<style>
  :root {
    --paper: #ffffff;
    --ink: #111111;
    --polo-blue: #3f6f8d;
    --denim-pink: #ec7f9d;
    --badge-pink: #f06b8f;
    --badge-pale: #fbe3ea;
    --badge-grey: #333333;
    --photo-boy-top: #6f9a72;
    --photo-boy-bottom: #a9bfd3;
    --photo-girl-top: #f1ebe7;
    --photo-girl-bottom: #5b889e;
  }
  html, body {
    margin: 0;
    padding: 0;
    overflow: hidden;
    background: var(--paper);
  }
  .banner {
    position: relative;
    width: 1200px;
    height: 603px;
    overflow: hidden;
    background: var(--paper);
  }
  .banner svg { display: block; }
  .brush-text {
    font-family: "Caveat Brush", "Gochi Hand", cursive;
    fill: var(--ink);
  }
  .hand-text {
    font-family: "Gochi Hand", "Caveat Brush", cursive;
  }
  .headline-line { font-size: 50px; }
  .headline-season { font-size: 54px; }
  .offer-lead { font-size: 28px; }
  .offer-figure { font-size: 120px; }
  .offer-percent { font-size: 44px; }
  .offer-tail { font-size: 28px; }
  .product-kicker { font-size: 21px; }
  .product-name { font-size: 44px; }
  .product-polo { fill: var(--polo-blue); }
  .product-dress { fill: var(--denim-pink); }
  .product-dress-name { font-size: 44px; fill: var(--denim-pink); }
  .code-label { font-family: "Arimo", sans-serif; font-size: 17px; fill: var(--badge-grey); }
  .code-value { font-family: "Arimo", sans-serif; font-weight: 400; font-size: 28px; fill: var(--ink); }
  .code-expiry { font-family: "Arimo", sans-serif; font-size: 10px; fill: var(--badge-grey); }
  .frame { fill: none; stroke: var(--ink); stroke-width: 8; stroke-linecap: round; stroke-linejoin: round; }
  .burst { stroke: var(--ink); stroke-width: 3; stroke-linecap: round; }
</style>
</head>
<body>
<div class="banner">
  <svg width="1200" height="603" viewBox="0 0 1200 603" xmlns="http://www.w3.org/2000/svg">
    <defs>
      <linearGradient id="boyTone" x1="0" y1="0" x2="0" y2="1">
        <stop offset="0" stop-color="var(--photo-boy-top)"/>
        <stop offset="1" stop-color="var(--photo-boy-bottom)"/>
      </linearGradient>
      <linearGradient id="girlTone" x1="0" y1="0" x2="0" y2="1">
        <stop offset="0" stop-color="var(--photo-girl-top)"/>
        <stop offset="1" stop-color="var(--photo-girl-bottom)"/>
      </linearGradient>
      <radialGradient id="badgeTone" cx="0.5" cy="0.5" r="0.5">
        <stop offset="0.62" stop-color="var(--badge-pale)"/>
        <stop offset="1" stop-color="var(--badge-pink)"/>
      </radialGradient>
    </defs>

    <path class="frame" d="M38 46 L420 42 L820 40 L1168 42 M1166 38 L1168 300 L1170 553 M1172 551 L800 548 L420 552 L36 557 M40 560 L38 300 L36 42"/>
    <path class="frame" d="M62 18 L60 48"/>

    <rect role="img" aria-label="Photo of a smiling boy in a green and black striped polo shirt and denim shorts"
          fill="url(#boyTone)" x="475" y="40" width="160" height="563" rx="40"/>
    <rect role="img" aria-label="Photo of a smiling girl with long hair in a white t-shirt and denim pinafore dress"
          fill="url(#girlTone)" x="885" y="8" width="270" height="595" rx="60"/>

    <g class="brush-text">
      <text class="headline-line" x="82" y="104" textLength="188" lengthAdjust="spacingAndGlyphs">Kick back</text>
      <text class="headline-line" x="74" y="160" textLength="262" lengthAdjust="spacingAndGlyphs">or kick it up</text>
      <text class="headline-line" x="92" y="220" textLength="240" lengthAdjust="spacingAndGlyphs">a notch this</text>
      <text class="headline-season" x="120" y="302" textLength="160" lengthAdjust="spacingAndGlyphs">Autumn</text>
    </g>
    <g class="burst">
      <line x1="98" y1="243" x2="110" y2="252"/>
      <line x1="136" y1="236" x2="140" y2="250"/>
      <line x1="178" y1="232" x2="180" y2="248"/>
      <line x1="218" y1="234" x2="216" y2="250"/>
      <line x1="258" y1="238" x2="252" y2="252"/>
      <line x1="292" y1="250" x2="282" y2="262"/>
      <line x1="80" y1="296" x2="100" y2="292"/>
      <line x1="290" y1="292" x2="312" y2="294"/>
      <line x1="118" y1="318" x2="108" y2="332"/>
      <line x1="178" y1="322" x2="176" y2="336"/>
      <line x1="226" y1="322" x2="228" y2="336"/>
      <line x1="262" y1="316" x2="272" y2="330"/>
    </g>

    <g class="brush-text">
      <text class="offer-lead" x="135" y="464" textLength="168" lengthAdjust="spacingAndGlyphs">Take a further</text>
      <text class="offer-figure" x="316" y="460" textLength="102" lengthAdjust="spacingAndGlyphs">40</text>
      <text class="offer-percent" x="426" y="460">%</text>
      <text class="offer-tail" x="312" y="500" textLength="140" lengthAdjust="spacingAndGlyphs">off all stock</text>
    </g>

    <text class="hand-text product-kicker product-polo" x="548" y="203" textLength="196" lengthAdjust="spacingAndGlyphs">versatile pique striped</text>
    <text class="hand-text product-name product-polo" x="576" y="245" textLength="172" lengthAdjust="spacingAndGlyphs">polo shirts</text>
    <text class="hand-text product-kicker product-dress" x="692" y="336" textLength="168" lengthAdjust="spacingAndGlyphs">Pinafore belt strap</text>
    <text class="brush-text product-dress-name" x="668" y="376" textLength="214" lengthAdjust="spacingAndGlyphs">Denim dress</text>

    <circle cx="845" cy="148" r="82" fill="url(#badgeTone)"/>
    <text class="code-label" x="845" y="116" text-anchor="middle">Use code:</text>
    <text class="code-value" x="845" y="158" text-anchor="middle" textLength="152" lengthAdjust="spacingAndGlyphs">TOVRELLI.</text>
    <text class="code-expiry" x="845" y="174" text-anchor="middle">Ends 31/12/2015</text>
  </svg>
</div>
</body>
</html>
```